Quorva - corporate Business Card

We need a good look and innovative business card for a new start up company based in Los Angeles called "Quorva". We are in a payment business, including payment card, app, and ewallet. We are expert in online payment and Card not present (CNP) transaction.
We need an innovative, modern business card.

Our logo font is Aero Matics

Target Market(s)

Startup - Bank - Online Payment - Card Manufacturing

Industry/Entity Type

Startup

Contact Information for Business Card

phone: 555 014 7396 - Address: 4172 Marlowe blvd, Ardenvale, NV 89299

Requirements
Must have
• Message: innovative, professional, expert, high tech, trust, online payment expert, security
Nice to have
• no comment
Should not have
• no Comment

```html
<!DOCTYPE html>
<html lang="en">
<head>
<meta charset="utf-8">
<title>Quorva – Business Card</title>
<link rel="stylesheet" href="https://fonts.googleapis.com/css2?family=Open+Sans:wght@400;600;700&display=swap">
<style>
  :root {
    --page-bg: #e9e6e2;
    --red-light: #b0323a;
    --red-mid: #9a1d26;
    --red-deep: #6e0a12;
    --frost-light: #f4f3f1;
    --frost-shade: #d9d6d2;
    --edge-silver: #b9b7b4;
    --text-light: #f3e9e9;
    --text-soft: #ead7d8;
    --brand-maroon: #7a0c14;
  }
  * { margin: 0; padding: 0; box-sizing: border-box; }
  html, body {
    width: 1200px;
    height: 970px;
    overflow: hidden;
    background: var(--page-bg);
    font-family: "Open Sans", Arial, sans-serif;
  }
  .card {
    position: absolute;
    left: 100px;
    top: 200px;
    width: 1000px;
    height: 568px;
    border-radius: 22px;
    overflow: hidden;
    box-shadow: 0 18px 40px rgba(0,0,0,0.18);
  }
  .card-surface {
    position: absolute;
    inset: 0;
  }
  .holder {
    position: absolute;
    left: 44px;
    top: 82px;
    color: var(--text-light);
  }
  .holder-name {
    font-weight: 600;
    font-size: 35px;
    line-height: 1.05;
  }
  .holder-title {
    font-weight: 400;
    font-size: 29px;
    line-height: 1.1;
    margin-left: -2px;
  }
  .address {
    position: absolute;
    left: 45px;
    top: 295px;
    color: var(--text-soft);
    font-size: 26px;
    line-height: 33px;
    font-style: normal;
  }
  .contact-list {
    position: absolute;
    left: 45px;
    top: 394px;
    list-style: none;
    color: var(--text-soft);
    font-size: 26px;
    line-height: 35px;
  }
  .contact-item {
    display: flex;
    align-items: center;
    gap: 12px;
  }
  .contact-icon {
    width: 31px;
    height: 31px;
    flex: none;
  }
  .brand {
    position: absolute;
    left: 522px;
    top: 205px;
    display: flex;
    align-items: center;
    gap: 14px;
  }
  .brand-dot {
    width: 130px;
    height: 130px;
    border-radius: 50%;
    background: var(--brand-maroon);
  }
  .brand-name {
    color: var(--brand-maroon);
    font-weight: 600;
    font-size: 84px;
    line-height: 1;
    letter-spacing: 1px;
  }
</style>
</head>
<body>
  <section class="card" aria-label="Quorva business card">
    <svg class="card-surface" width="1000" height="568" viewBox="0 0 1000 568" aria-hidden="true">
      <defs>
        <linearGradient id="frost" x1="0" y1="0" x2="1" y2="1">
          <stop offset="0" stop-color="var(--frost-light)"/>
          <stop offset="1" stop-color="var(--frost-shade)"/>
        </linearGradient>
        <linearGradient id="redPanel" x1="0" y1="0" x2="1" y2="0">
          <stop offset="0" stop-color="var(--red-light)"/>
          <stop offset="0.6" stop-color="var(--red-mid)"/>
          <stop offset="1" stop-color="var(--red-deep)"/>
        </linearGradient>
      </defs>
      <rect class="frost-panel" width="1000" height="568" fill="url(#frost)"/>
      <path class="edge-arc" d="M524 0 Q392 284 524 568 L514 568 Q382 284 514 0 Z" fill="var(--edge-silver)"/>
      <path class="red-panel" d="M0 0 H518 Q386 284 518 568 H0 Z" fill="url(#redPanel)"/>
      <circle class="edge-notch" cx="0" cy="118" r="30" fill="var(--edge-silver)"/>
    </svg>

    <header class="holder">
      <h1 class="holder-name">Dana Holt</h1>
      <p class="holder-title">Managing Director</p>
    </header>

    <address class="address">4172 Marlowe blvd,<br>Ardenvale, NV 89299</address>

    <ul class="contact-list">
      <li class="contact-item">
        <svg class="contact-icon" viewBox="0 0 32 32" aria-hidden="true">
          <circle cx="16" cy="16" r="15" fill="var(--text-soft)" opacity="0.75"/>
          <path d="M9 13 Q16 7 23 13 L21 15 L18 13 L14 13 L11 15 Z" fill="var(--red-mid)"/>
          <rect x="10" y="16" width="12" height="7" rx="1.5" fill="var(--red-mid)"/>
        </svg>
        <span>555 014 7396</span>
      </li>
      <li class="contact-item">
        <svg class="contact-icon" viewBox="0 0 32 32" aria-hidden="true">
          <circle cx="16" cy="16" r="15" fill="var(--text-soft)" opacity="0.75"/>
          <rect x="8" y="10.5" width="16" height="11" fill="none" stroke="var(--red-mid)" stroke-width="1.8"/>
          <path d="M8 10.5 L16 17 L24 10.5" fill="none" stroke="var(--red-mid)" stroke-width="1.8"/>
        </svg>
        <span>contact@quorvamail.com</span>
      </li>
    </ul>

    <div class="brand">
      <span class="brand-dot" aria-hidden="true"></span>
      <span class="brand-name">quorva</span>
    </div>
  </section>
</body>
</html>
```